Verdel Harvest - Stationery Design Project

We need a stationary for our business. We grow roots and fruits in Central and South America, we import and distribute in FL, USA. We do fresh and frozen products.

Target Market(s)

Small and big supermarkets, wholesalers, traders, distributors, etc

Industry/Entity Type

Business

```html
<!DOCTYPE html>
<html lang="en">
<head>
<meta charset="utf-8">
<title>Verdel Harvest – Stationery</title>
<link rel="stylesheet" href="https://fonts.googleapis.com/css2?family=Questrial&family=Montserrat:wght@500;600&display=swap">
<style>
  :root{
    --bg-top:#eef1f2;
    --bg-bottom:#d3d9dc;
    --paper:#ffffff;
    --paper-back:#eeefef;
    --ink:#3b3b3b;
    --ink-soft:#555;
    --rule:#8d8d8d;
    --brand-green:#4b5b26;
    --brand-orange:#e17d12;
    --shadow:rgba(0,0,0,.28);
  }
  *{margin:0;padding:0;box-sizing:border-box}
  html,body{width:1200px;height:927px;overflow:hidden}
  body{
    position:relative;
    background:linear-gradient(180deg,var(--bg-top) 0%,var(--bg-bottom) 100%);
    font-family:"Questrial",sans-serif;
    color:var(--ink);
  }
  .sheet{
    position:absolute;top:45px;width:512px;height:696px;
    border-radius:14px;
    box-shadow:0 1px 4px var(--shadow);
  }
  .sheet--front{left:43px;background:var(--paper)}
  .sheet--back{left:635px;background:linear-gradient(160deg,#f4f4f4,var(--paper-back))}

  .brand{
    position:absolute;display:flex;align-items:center;gap:9px;
    font-family:"Questrial",sans-serif;font-size:27px;letter-spacing:.5px;
    color:var(--brand-green);white-space:nowrap;
  }
  .brand__dot{width:14px;height:14px;border-radius:50%;background:var(--brand-green)}
  .sheet--front .brand{left:50%;top:40px;transform:translateX(-50%)}
  .sheet--back .brand{left:50%;top:600px;transform:translateX(-50%)}

  .web-rule{
    position:absolute;left:47px;top:98px;width:426px;
    display:flex;align-items:center;gap:8px;
  }
  .web-rule__line{flex:1;height:2px;background:var(--rule)}
  .web-rule__url{
    font-family:"Montserrat",sans-serif;font-weight:600;font-size:10px;
    letter-spacing:1.4px;color:var(--ink)
  }
  .web-rule__url span{color:var(--brand-orange)}

  .letter-body{
    position:absolute;left:44px;top:143px;width:426px;
    font-size:10.4px;line-height:17.6px;text-align:justify;color:var(--ink-soft);
  }
  .letter-body p{margin-bottom:17.6px}

  .signature{position:absolute;left:380px;top:583px}
  .signature__name{font-size:13px;color:var(--ink)}
  .signature__title{font-size:9px;margin-top:6px;color:var(--ink)}

  .contact-bar{
    position:absolute;left:26px;right:38px;top:673px;
    display:flex;justify-content:space-between;
    font-family:"Montserrat",sans-serif;font-weight:600;font-size:9.3px;color:#222;
  }

  .features{
    position:absolute;left:33px;top:805px;list-style:none;
    font-family:"Questrial",sans-serif;font-size:25px;line-height:34px;
    text-transform:uppercase;color:#1d1d1d;letter-spacing:.3px;
  }
</style>
</head>
<body>
  <section class="sheet sheet--front" aria-label="Letterhead front">
    <div class="brand"><span class="brand__dot"></span>Verdel Harvest</div>
    <div class="web-rule">
      <span class="web-rule__line"></span>
      <span class="web-rule__url">www.<span>verdelharvest</span>.com</span>
      <span class="web-rule__line"></span>
    </div>
    <div class="letter-body">
      <p>Lorem ipsum dolor sit amet, consectetur adipiscing elit. Donec orci purus, luctus vitae dignissim eu, iaculis sed purus. Vivamus faucibus, ipsum nec aliquet viverra, leo mauris condimentum ligula, sit amet sagittis enim ligula quis arcu. Nam egestas tortor id nisi porttitor mattis. In tortor ante, ultricies in suscipit a, tempus non massa. Vivamus et auctor mi. Fusce vel massa nulla. Phasellus nec eros mauris, et scelerisque orci. Donec malesuada orci vitae nulla accumsan porta a id massa.</p>
      <p>Quisque accumsan iaculis magna sit amet fringilla. Maecenas consequat, magna eget tincidunt semper, odio nibh rutrum mi, id feugiat ante nisi eu risus. Vestibulum nunc orci, rhoncus a placerat in, ultricies in mi. Cras mattis varius eros, vel fringilla nisi suscipit eget. Quisque scelerisque sagittis nulla at porttitor. Mauris a justo et tellus interdum tristique. Sed id augue vitae urna euismod commodo aliquet a quam. Pellentesque arcu velit, cursus et malesuada ut, consequat et diam. Nullam erat sem, rhoncus id ullamcorper vitae, rhoncus et arcu. In ultricies ultricies nulla,</p>
      <p>Kut rutrum nisi iaculis at. Donec eu magna a metus ornare faucibus. Fusce aliquet faucibus ultricies. Morbi semper, est id tincidunt gravida, sem arcu adipiscing lacus, ac bibendum nulla leo eu purus. Quisque nec diam sed risus consectetur a ccumsan quis quis nibh. Vestibulum id purus lorem. Donec eu magna a metus ornare faucibus. Fusce aliquet faucibus ultricies. Morbi semper, est id tincidunt gravida, sem arcu adipiscing lacus, ac bibendum nulla leo eu purus. Quisque nec diam sed risus consectetur a ccumsan quis quis nibh. Vestibulum id purus lorem.</p>
    </div>
    <div class="signature">
      <div class="signature__name">Elena Ruiz</div>
      <div class="signature__title">Co-Founder &amp; CEO</div>
    </div>
    <div class="contact-bar">
      <span>Ph: 305.418.2260</span>
      <span>Fax: 305.418.2261</span>
      <span>Toll Free: 888.502.3170</span>
    </div>
  </section>

  <section class="sheet sheet--back" aria-label="Letterhead back">
    <div class="brand"><span class="brand__dot"></span>Verdel Harvest</div>
  </section>

  <ul class="features">
    <li>- Print ready &amp; editable files</li>
    <li>- PSD, JPG, TIFF, PNG, AI, EPS&nbsp; file formats</li>
    <li>- Unlimited revisions are most welcome</li>
  </ul>
</body>
</html>
```